RWT Fittings Ltd Business Cards

We need a business card with our business logo. We provide window and door installations on high-rises in west coast British Colombia, Canada.

I would like my business information and details on one side of the card, and the other side the company name with logo

Target Market(s)

General Contractors

Industry/Entity Type

Construction

Contact Information for Business Card

one side i want my company name and logo in the dark theme logo that i provided

Requirements
Must have
• Marco Peltieri, 16045518293, RWTFittings@mailbox-demo.com, 1407-5194 Linden Row Burnaby BC, V5H 2K9, Owner & Manager

```html
<!DOCTYPE html>
<html lang="en">
<head>
<meta charset="utf-8">
<title>RWT Fittings Ltd – Business Cards</title>
<link rel="stylesheet" href="https://fonts.googleapis.com/css2?family=Roboto:wght@400;700&display=swap">
<style>
  :root {
    --page-bg: #232323;
    --card-dark: #1e1e22;
    --band-grey: #9a9a9a;
    --band-blue: #29a9e1;
    --text-white: #ffffff;
    --text-soft: #f0f0f0;
    --brand-blue: #3cb4e6;
    --brand-grey: #8d8a86;
    --photo-deep: #1c1a18;
    --photo-warm: #4a443e;
  }
  * { margin: 0; padding: 0; box-sizing: border-box; }
  html, body {
    width: 1200px; height: 780px; overflow: hidden;
    background: var(--page-bg);
    font-family: 'Roboto', Arial, sans-serif;
  }
  .sheet {
    position: relative; width: 1200px; height: 780px;
    display: flex; align-items: center; justify-content: center; gap: 50px;
  }
  .card {
    position: relative; width: 540px; height: 310px;
    overflow: hidden; border-radius: 3px;
    box-shadow: 0 18px 40px rgba(0,0,0,.55);
  }

  /* Contact side */
  .card--contact { background: var(--card-dark); }
  .brand {
    position: absolute; display: flex; align-items: center; gap: 10px;
    font-weight: 700; color: var(--brand-blue); white-space: nowrap;
  }
  .brand__mark { width: 22px; height: 22px; background: var(--brand-grey); }
  .card--contact .brand { left: 230px; top: 80px; font-size: 26px; }

  .name-band {
    position: absolute; left: 0; top: 158px; width: 210px; height: 84px;
    background: var(--band-grey);
    padding: 16px 0 0 24px; color: var(--text-white);
  }
  .name-band__name { font-size: 23px; font-weight: 700; line-height: 1.1; }
  .name-band__role { font-size: 12.5px; margin-top: 6px; }

  .contact-band {
    position: absolute; right: 0; top: 186px; width: 262px; height: 72px;
    background: var(--band-blue); color: var(--text-white);
    padding: 14px 0 0 18px; font-size: 12.5px; line-height: 1.55;
  }
  .contact-band__row { display: flex; align-items: center; gap: 8px; white-space: nowrap; }
  .contact-band__row svg { width: 12px; height: 12px; flex: none; }

  .address {
    position: absolute; left: 60px; bottom: 18px;
    font-size: 12.5px; color: var(--text-soft); white-space: nowrap;
  }

  /* Brand side */
  .card--brand { background: var(--photo-deep); }
  .backdrop {
    position: absolute; inset: 0;
    background:
      radial-gradient(ellipse at 72% 55%, var(--photo-warm) 0%, transparent 60%),
      linear-gradient(135deg, var(--photo-deep) 0%, #2e2a26 55%, #3a3530 100%);
  }
  .card--brand .brand {
    left: 50%; top: 50%; transform: translate(-50%, -50%); font-size: 30px;
  }
</style>
</head>
<body>
<main class="sheet">
  <section class="card card--contact">
    <div class="brand"><span class="brand__mark"></span>RWT Fittings Ltd</div>

    <div class="name-band">
      <p class="name-band__name">Marco Peltieri</p>
      <p class="name-band__role">Owner &amp; Manager</p>
    </div>

    <div class="contact-band">
      <p class="contact-band__row">
        <svg viewBox="0 0 24 24" aria-hidden="true"><path fill="#fff" d="M6.6 10.8a15.1 15.1 0 0 0 6.6 6.6l2.2-2.2c.3-.3.7-.4 1-.2 1.1.4 2.3.6 3.6.6.6 0 1 .4 1 1V20c0 .6-.4 1-1 1A17 17 0 0 1 3 4c0-.6.4-1 1-1h3.5c.6 0 1 .4 1 1 0 1.3.2 2.5.6 3.6.1.3 0 .7-.2 1z"/></svg>
        1604 551 8293
      </p>
      <p class="contact-band__row">
        <svg viewBox="0 0 24 24" aria-hidden="true"><path fill="#fff" d="M3 5h18v14H3z"/><path fill="none" stroke="#29a9e1" stroke-width="2" d="M3 6l9 7 9-7"/></svg>
        RWTFittings@mailbox-demo.com
      </p>
    </div>

    <p class="address">1407-5194 Linden Row Burnaby BC, V5H 2K9</p>
  </section>

  <section class="card card--brand">
    <div class="backdrop" role="img" aria-label="Soft blurred interior photograph in dark warm tones"></div>
    <div class="brand"><span class="brand__mark"></span>RWT Fittings Ltd</div>
  </section>
</main>
</body>
</html>
```